Corporate web site design for a blockchain oriented company

Design a web site for Velmora. The company works on blockchain projects, mostly in B2B . Logo and content of the web site are attached with the project.

Corporate web sites means that we need to present the company and, at least, two of its projects.

Target Market(s)

B2B (Telecom, Gvt, online e-commerce web sites, banks, insurance ...)

Number of Pages Required

3 page

Font styles to use
Sans Serif

Requirements
Must have
• Landing page
• Page for KYC product
• Page for Loyalty product
• Team presentation
• Contact form
• Company presentation
• Several section can be in one page.
Nice to have
• Teaser video per project.
Should not have
• Heavy web site with a lot of animations.

```html
<!DOCTYPE html>
<html lang="en">
<head>
<meta charset="utf-8">
<title>Velmora — Blockchain Solutions</title>
<link href="https://fonts.googleapis.com/css2?family=Montserrat:wght@400;500;600;700&family=Open+Sans:wght@400;600&display=swap" rel="stylesheet">
<style>
  :root {
    --ink: #111111;
    --text: #222222;
    --muted: #555555;
    --white: #ffffff;
    --btn: #262626;
    --panel-dark: #e4e4e4;
    --panel-light: #efefef;
    --band: #f0f0f0;
    --line: #c9c9c9;
    --footer: #161616;
    --footer-alt: #2b2b2b;
    --hero-a: #0a1b20;
    --hero-b: #163a40;
    --hero-c: #4a3a1a;
  }
  * { box-sizing: border-box; margin: 0; padding: 0; }
  html, body { width: 1200px; height: 3169px; overflow: hidden; }
  body { position: relative; background: var(--white); color: var(--text); font-family: "Montserrat", sans-serif; }
  .abs { position: absolute; }

  /* Header */
  .site-header { position: absolute; left: 0; top: 0; width: 1200px; height: 89px; background: var(--white); }
  .brand { position: absolute; left: 144px; top: 20px; display: flex; align-items: center; gap: 14px; font-family: "Montserrat", sans-serif; font-weight: 500; font-size: 42px; letter-spacing: 3px; color: var(--ink); }
  .brand-mark { width: 14px; height: 14px; background: var(--ink); }
  .main-nav { position: absolute; right: 144px; top: 34px; display: flex; gap: 30px; font-size: 14px; color: var(--ink); }
  .main-nav a { color: inherit; text-decoration: none; }
  .main-nav a.is-active { border-bottom: 1px solid var(--ink); padding-bottom: 3px; }

  /* Hero */
  .hero { position: absolute; left: 0; top: 89px; width: 1200px; height: 526px; }
  .hero-media { position: absolute; inset: 0; background: radial-gradient(ellipse at 45% 55%, var(--hero-c) 0%, rgba(74,58,26,0) 25%), linear-gradient(120deg, var(--hero-a) 0%, var(--hero-b) 60%, var(--hero-a) 100%); }
  .hero-play { position: absolute; left: 580px; top: 218px; width: 40px; height: 40px; }
  .hero-title { position: absolute; left: 0; top: 268px; width: 1200px; text-align: center; color: var(--white); font-weight: 700; font-size: 40px; letter-spacing: 0.5px; }

  /* Buttons */
  .btn { position: absolute; display: inline-block; background: var(--btn); color: var(--white); font-family: "Montserrat", sans-serif; font-size: 14px; font-weight: 500; text-align: center; line-height: 44px; height: 44px; width: 120px; }

  /* About */
  .about-title { left: 144px; top: 732px; font-size: 31px; font-weight: 700; color: var(--ink); }
  .about-text { left: 144px; top: 786px; width: 445px; font-size: 14.5px; line-height: 27px; color: var(--text); }
  .about-btn { left: 144px; top: 968px; }
  .about-media { left: 634px; top: 697px; width: 420px; height: 350px; }

  /* Products */
  .products { position: absolute; left: 0; top: 1130px; width: 1200px; height: 560px; }
  .products svg.bg { position: absolute; inset: 0; }
  .product-icon { position: absolute; }
  .product-title { position: absolute; font-size: 31px; font-weight: 700; color: var(--ink); }
  .product-sub { position: absolute; font-size: 20px; font-weight: 400; color: var(--ink); }
  .product-text { position: absolute; width: 300px; font-size: 14.5px; line-height: 27px; color: var(--text); }
  .is-right { text-align: right; }

  /* Section titles */
  .section-title { position: absolute; left: 0; width: 1200px; text-align: center; font-size: 31px; font-weight: 700; color: var(--ink); }

  /* Team */
  .carousel-arrow { position: absolute; width: 20px; height: 30px; }
  .member { position: absolute; width: 240px; text-align: center; }
  .member-photo { display: block; margin: 0 auto; width: 210px; height: 200px; }
  .member-name { margin-top: 18px; font-size: 20px; font-weight: 500; color: var(--ink); }
  .member-role { margin-top: 4px; font-family: "Open Sans", sans-serif; font-size: 13px; color: var(--text); }

  /* Blog */
  .blog { position: absolute; left: 0; top: 2166px; width: 1200px; height: 461px; background: var(--band); }
  .blog-card { position: absolute; left: 144px; top: 2290px; width: 910px; height: 256px; background: var(--white); }
  .blog-media { position: absolute; left: 0; top: 0; width: 456px; height: 256px; background: radial-gradient(ellipse at 60% 50%, #3fb4e6 0%, #1564b0 45%, #0a2d6a 100%); }
  .blog-title { position: absolute; left: 482px; top: 28px; font-size: 17px; font-weight: 500; color: var(--ink); }
  .blog-date { position: absolute; left: 482px; top: 64px; font-family: "Open Sans", sans-serif; font-size: 12px; color: var(--ink); }
  .blog-text { position: absolute; left: 482px; top: 88px; width: 400px; font-family: "Open Sans", sans-serif; font-size: 11.5px; line-height: 19px; color: var(--muted); }
  .blog-btn { left: 482px; top: 182px; }

  /* Contact */
  .field { position: absolute; border: 1px solid var(--line); background: var(--white); font-family: "Open Sans", sans-serif; font-size: 12px; color: var(--muted); padding: 12px 16px; }
  .submit-btn { left: 541px; top: 2950px; width: 118px; }

  /* Footer */
  .site-footer { position: absolute; left: 0; top: 3070px; width: 1200px; height: 99px; }
  .site-footer svg.bg { position: absolute; inset: 0; }
  .footer-nav { position: absolute; left: 144px; top: 26px; font-family: "Open Sans", sans-serif; font-size: 11.5px; color: #d8d8d8; word-spacing: 4px; }
  .footer-copy { position: absolute; left: 144px; top: 56px; font-family: "Open Sans", sans-serif; font-size: 11.5px; color: #bdbdbd; }
  .social { position: absolute; top: 36px; width: 16px; height: 16px; border-radius: 50%; background: #d8d8d8; }
</style>
</head>
<body>

<header class="site-header">
  <div class="brand"><span>Velmora</span><span class="brand-mark"></span></div>
  <nav class="main-nav">
    <a class="is-active" href="#">Home</a>
    <a href="#">About us</a>
    <a href="#">KYC Product</a>
    <a href="#">Loyalty Product</a>
    <a href="#">Team</a>
    <a href="#">Contact us</a>
  </nav>
</header>

<section class="hero">
  <div class="hero-media" role="img" aria-label="Dark teal abstract network scene with a glowing geometric cube"></div>
  <svg class="hero-play" viewBox="0 0 40 40" aria-hidden="true">
    <circle cx="20" cy="20" r="19" fill="#ffffff"/>
    <polygon points="15,11 30,20 15,29" fill="#0a1b20"/>
  </svg>
  <h1 class="hero-title">TEASER VIDEO</h1>
</section>

<h2 class="abs about-title">ABOUT VELMORA</h2>
<p class="abs about-text">Velmora Technology is a technology enabler that pledges to tackle issues that have plagued organisations for years. The company is lead by a team with tremendous expertise in the field of blockchain, mobile, IT, payment and financial sector. Being a global team, the company has influence in Singapore, China , France and more.</p>
<a class="btn about-btn">Read More</a>
<svg class="abs about-media" viewBox="0 0 420 350" role="img" aria-label="Photo of a steel chain link with digital texture inside a triangle">
  <defs>
    <linearGradient id="chainGrad" x1="0" y1="0" x2="1" y2="1">
      <stop offset="0" stop-color="#cfd6dc"/>
      <stop offset="0.5" stop-color="#4f6474"/>
      <stop offset="1" stop-color="#1d2a36"/>
    </linearGradient>
  </defs>
  <polygon points="0,0 420,0 210,280" fill="url(#chainGrad)"/>
</svg>

<section class="products">
  <svg class="bg" viewBox="0 0 1200 560" aria-hidden="true">
    <rect x="0" y="16" width="1200" height="544" fill="var(--panel-light)"/>
    <polygon points="0,0 686,0 560,560 0,560" fill="var(--panel-dark)"/>
    <polygon points="686,0 686,16 540,560 516,560" fill="#d6d6d6"/>
  </svg>

  <svg class="product-icon" style="left:144px; top:96px;" width="76" height="80" viewBox="0 0 76 80" fill="none" stroke="#222" stroke-width="2.5" aria-hidden="true">
    <rect x="3" y="6" width="30" height="30"/><rect x="41" y="6" width="30" height="30"/>
    <rect x="3" y="44" width="30" height="30"/><rect x="41" y="44" width="30" height="30"/>
    <path d="M3 6 L9 1 H39 L33 6 M41 6 L47 1 H75 L71 6"/>
  </svg>
  <h3 class="product-title" style="left:144px; top:204px;">KYC PRODUCT</h3>
  <p class="product-sub" style="left:144px; top:256px;">Own your identity</p>
  <p class="product-text" style="left:144px; top:298px;">KYC , or "Know Your Customer", is a process of verifying the identity of account holders, either before or during the time where business done.</p>
  <a class="btn" style="left:144px; top:427px;">Read More</a>

  <svg class="product-icon" style="left:972px; top:96px;" width="82" height="82" viewBox="0 0 82 82" fill="none" stroke="#222" stroke-width="5" stroke-linecap="round" aria-hidden="true">
    <rect x="8" y="32" width="42" height="22" rx="11" transform="rotate(-45 29 43)"/>
    <rect x="32" y="28" width="42" height="22" rx="11" transform="rotate(-45 53 39)"/>
  </svg>
  <h3 class="product-title is-right" style="right:146px; top:204px;">LOYALTY PRODUCT</h3>
  <p class="product-sub is-right" style="right:146px; top:256px;">Intuitive partnership solution</p>
  <p class="product-text is-right" style="right:146px; top:298px;">In this day and age, majority of the businesses are offering loyalty programs to bring in returning customers.</p>
  <a class="btn" style="left:936px; top:427px;">Read More</a>
</section>

<h2 class="section-title" style="top:1768px;">TEAM</h2>
<svg class="carousel-arrow" style="left:53px; top:1913px;" viewBox="0 0 20 30" aria-hidden="true"><path d="M15 4 L5 15 L15 26" fill="none" stroke="#666" stroke-width="2"/></svg>
<svg class="carousel-arrow" style="left:1127px; top:1913px;" viewBox="0 0 20 30" aria-hidden="true"><path d="M5 4 L15 15 L5 26" fill="none" stroke="#666" stroke-width="2"/></svg>

<div class="member" style="left:172px; top:1827px;">
  <svg class="member-photo" viewBox="0 0 210 200" role="img" aria-label="Portrait photo of John Cole">
    <polygon points="105,0 205,100 105,200 5,100" fill="#dcdcdc"/>
    <polygon points="120,0 210,90 120,180 30,90" fill="#7b7f86"/>
  </svg>
  <p class="member-name">John Cole</p>
  <p class="member-role">Aliquam erat volutpat</p>
</div>
<div class="member" style="left:480px; top:1827px;">
  <svg class="member-photo" viewBox="0 0 210 200" role="img" aria-label="Portrait photo of Emily">
    <polygon points="105,0 205,100 105,200 5,100" fill="#dcdcdc"/>
    <polygon points="120,0 210,90 120,180 30,90" fill="#b9a08a"/>
  </svg>
  <p class="member-name">Emily</p>
  <p class="member-role">Duis hendrerit arcu</p>
</div>
<div class="member" style="left:786px; top:1827px;">
  <svg class="member-photo" viewBox="0 0 210 200" role="img" aria-label="Portrait photo of William">
    <polygon points="105,0 205,100 105,200 5,100" fill="#dcdcdc"/>
    <polygon points="120,0 210,90 120,180 30,90" fill="#6d6a68"/>
  </svg>
  <p class="member-name">William</p>
  <p class="member-role">Pellentesque vehicula</p>
</div>

<section class="blog"></section>
<h2 class="section-title" style="top:2234px;">BLOG</h2>
<svg class="carousel-arrow" style="left:53px; top:2403px;" viewBox="0 0 20 30" aria-hidden="true"><path d="M15 4 L5 15 L15 26" fill="none" stroke="#666" stroke-width="2"/></svg>
<svg class="carousel-arrow" style="left:1127px; top:2403px;" viewBox="0 0 20 30" aria-hidden="true"><path d="M5 4 L15 15 L5 26" fill="none" stroke="#666" stroke-width="2"/></svg>
<article class="blog-card">
  <div class="blog-media" role="img" aria-label="Photo of glowing blue digital chain links"></div>
  <h3 class="blog-title">Nam suscipit sapien eget blandit sollicitudin</h3>
  <p class="blog-date">14 January, 2019</p>
  <p class="blog-text">Aliquam malesuada eros sit amet turpis scelerisque maximus. Maecenas lobortis iaculis efficitur. Nulla facilisi. Vestibulum pharetra diam ex, in posuere purus efficitur ac. Mauris placerat eros lorem, vel egestas mi mattis eget. Donec a nisl vel ante tristique mollis nec quis est.</p>
  <a class="btn blog-btn">Read More</a>
</article>

<h2 class="section-title" style="top:2696px;">CONTACT US</h2>
<div class="field" style="left:351px; top:2753px; width:241px; height:43px;">Name</div>
<div class="field" style="left:606px; top:2753px; width:241px; height:43px;">Email</div>
<div class="field" style="left:351px; top:2812px; width:496px; height:119px;">Message</div>
<a class="btn submit-btn">Submit</a>

<footer class="site-footer">
  <svg class="bg" viewBox="0 0 1200 99" aria-hidden="true">
    <rect width="1200" height="99" fill="var(--footer)"/>
    <polygon points="613,0 1200,0 1200,99 575,99" fill="var(--footer-alt)"/>
  </svg>
  <p class="footer-nav">Home &nbsp;|&nbsp; About us &nbsp;|&nbsp; KYC Product &nbsp;|&nbsp; Loyalty Product &nbsp;|&nbsp; Team &nbsp;|&nbsp; Contact us</p>
  <p class="footer-copy">Copyright © 2019 Velmora. All rights reserved.</p>
  <span class="social" style="left:1002px;"></span>
  <span class="social" style="left:1036px;"></span>
</footer>

</body>
</html>
```